Harborline Claims Advocates Business card

We need to get business card Design for our Company we are Public Adjusters in Chicago Illinois - i like to see good combination and elements from my Company Logo. as well To be an two side design
Updates

Target Market(s)

Home /Business owner Property Managers

Industry/Entity Type

Business

Contact Information for Business Card

to show the Element of our logo i will Like 3D

Font styles to use
Sans Serif

Requirements
Must have
• Logo and Element of the Logo in 3D
Nice to have
• Logo That we Provide 3D Same Colors or open for suggestions
Should not have
• unleare view -

```html
<!DOCTYPE html>
<html lang="en">
<head>
<meta charset="utf-8">
<title>Harborline Claims Advocates — Business Card</title>
<link href="https://fonts.googleapis.com/css2?family=Open+Sans:wght@400;600;700&display=swap" rel="stylesheet">
<style>
  :root {
    --backdrop: #e6e6e6;
    --card-white: #ffffff;
    --brand-orange: #e2583a;
    --brand-navy: #1a22b4;
    --brand-red: #d2392a;
    --band-dark: #0a0e3e;
    --band-bright: #1444d6;
    --text-grey: #4a4a4a;
    --divider: #d4d4d4;
  }
  * { margin: 0; padding: 0; box-sizing: border-box; }
  html, body { width: 1200px; height: 987px; overflow: hidden; }
  body {
    background: var(--backdrop);
    font-family: "Open Sans", Arial, sans-serif;
    position: relative;
  }
  .card {
    position: absolute;
    width: 615px;
    height: 352px;
    box-shadow: 0 2px 6px rgba(0,0,0,0.18);
    overflow: hidden;
  }
  .card-front { left: 293px; top: 130px; background: var(--card-white); }
  .card-back { left: 292px; top: 505px; background: var(--brand-orange); }

  .brand-block {
    position: absolute;
    left: 30px; top: 0; width: 280px; height: 328px;
    display: flex; align-items: center; justify-content: center;
  }
  .brand-name {
    font-weight: 700; font-size: 22px; color: var(--brand-navy);
    text-align: center; line-height: 1.3;
  }

  .front-divider {
    position: absolute; left: 320px; top: 60px; width: 1px; height: 230px;
    background: var(--divider);
  }
  .contact-block { position: absolute; left: 355px; top: 62px; color: var(--text-grey); }
  .person-name { font-weight: 600; font-size: 22px; color: var(--brand-navy); letter-spacing: 0.3px; line-height: 1.1; }
  .person-title { font-size: 16px; color: var(--brand-red); margin-top: 4px; }
  .address { font-size: 15.5px; line-height: 23px; margin-top: 12px; }
  .contact-list { list-style: none; margin-top: 7px; }
  .contact-list li { display: flex; align-items: center; gap: 8px; font-size: 15.5px; height: 23.5px; white-space: nowrap; }
  .contact-list svg { width: 15px; height: 15px; fill: var(--brand-navy); flex: none; }

  .front-band { position: absolute; left: 0; bottom: 0; width: 615px; height: 24px; }

  .back-brand {
    position: absolute; left: 0; top: 95px; width: 615px; height: 140px;
    display: flex; align-items: center; justify-content: center;
  }
  .back-brand .brand-name { font-size: 30px; }
  .back-rule {
    position: absolute; left: 95px; top: 271px; width: 433px; height: 1px;
    background: linear-gradient(90deg, transparent, var(--brand-navy) 30%, var(--brand-navy) 70%, transparent);
  }
  .back-url {
    position: absolute; left: 0; top: 284px; width: 615px; text-align: center;
    color: #ffffff; font-size: 16px; letter-spacing: 2.4px;
  }
</style>
</head>
<body>

<section class="card card-front">
  <div class="brand-block">
    <div class="brand-name">Harborline Claims<br>Advocates</div>
  </div>

  <div class="front-divider"></div>

  <div class="contact-block">
    <div class="person-name">DANA WHITFIELD</div>
    <div class="person-title">CEO/Founder</div>
    <div class="address">214 Larkspur Court<br>Chicago, Illinois 60614</div>
    <ul class="contact-list">
      <li><svg viewBox="0 0 16 16"><path d="M3.5 1.5l2.5 0 1.2 3.2-1.6 1.2a8 8 0 0 0 4.5 4.5l1.2-1.6 3.2 1.2 0 2.5c0 .8-.7 1.5-1.5 1.5A12.5 12.5 0 0 1 2 3c0-.8.7-1.5 1.5-1.5z"/></svg>312 555 0147</li>
      <li><svg viewBox="0 0 16 16"><path d="M4.5 0.5h7a1 1 0 0 1 1 1v13a1 1 0 0 1-1 1h-7a1 1 0 0 1-1-1v-13a1 1 0 0 1 1-1zm1 2v9.5h5V2.5zm2.5 10.5a1 1 0 1 0 0 2 1 1 0 0 0 0-2z"/></svg>312 555 0193</li>
      <li><svg viewBox="0 0 16 16"><path d="M4 1h8v4H4zM1 6h14v7h-2v2H3v-2H1zm4 5v3h6v-3z"/></svg>312 555 0126</li>
      <li><svg viewBox="0 0 16 16"><path d="M1 3h14v10H1zm1.3 1.2L8 8.6l5.7-4.4z"/></svg>dana@harborlineclaims.com</li>
      <li><svg viewBox="0 0 16 16"><path d="M8 1a7 7 0 1 0 0 14A7 7 0 0 0 8 1zm0 1.5a5.5 5.5 0 1 1 0 11 5.5 5.5 0 0 1 0-11zM2.5 8h11M8 2.5c-2 2-2 9 0 11M8 2.5c2 2 2 9 0 11" stroke="var(--brand-navy)" stroke-width="1.2" fill="none"/></svg>www.harborlineclaims.com</li>
    </ul>
  </div>

  <svg class="front-band" viewBox="0 0 615 24" preserveAspectRatio="none" aria-hidden="true">
    <defs>
      <linearGradient id="bandBlue" x1="0" x2="1" y1="0" y2="0">
        <stop offset="0" stop-color="#0a0e3e"/>
        <stop offset="0.55" stop-color="#1444d6"/>
        <stop offset="1" stop-color="#0a0e3e"/>
      </linearGradient>
    </defs>
    <polygon points="0,0 399,0 392,24 0,24" fill="url(#bandBlue)"/>
    <polygon points="406,0 615,0 615,24 399,24" fill="#e2583a"/>
  </svg>
</section>

<section class="card card-back">
  <div class="back-brand">
    <div class="brand-name">Harborline Claims<br>Advocates</div>
  </div>
  <div class="back-rule"></div>
  <div class="back-url">www.HarborlineClaimsAdvocates.com</div>
</section>

</body>
</html>
```